Business Card Makeover. Recreate a sleek modern design for our business card.

DO NOT COPY OUR CURRENT DESIGN. MUST BE ONE SIDED BUSINESS CARD.
Create a new business card design, using our new logo. Attached is a sample of our current design and new logo. Please note the address and email will change. The new address is 412 Corvell West Palm Beach 33401 and our website will be www.delmarhollis.example.

We are an architectural and interior design firm. We prefer a clean modern look. Something that is refined and emulates excellence.

Industry/Entity Type

Architecture

Contact Information for Business Card

clean modern look, please do not copy our attached design.

Font styles to use
Other font styles liked:
• see attached business card font

Colors

Designer to choose colors to be used in the design.

Requirements
Must have
• Must have a modern appeal and resemble our current branding.
Nice to have
• modern font, our logo, legible name and titles progressive design
Should not have
• Do not add colors not reflected in our branding. Should not look like our current card.

```html
<!DOCTYPE html>
<html lang="en">
<head>
<meta charset="utf-8">
<title>Delmar Hollis + Partners — Business Card</title>
<link rel="stylesheet" href="https://fonts.googleapis.com/css2?family=Lato:wght@400;900&display=swap">
<style>
  :root {
    --brand-blue: #0b63ad;
    --ink: #1f1f1f;
    --card: #ffffff;
    --backdrop: #e6e7e9;
  }
  * { margin: 0; padding: 0; box-sizing: border-box; }
  html, body {
    width: 1200px;
    height: 900px;
    overflow: hidden;
    background: var(--backdrop);
    font-family: "Lato", sans-serif;
    color: var(--ink);
  }
  .stage {
    width: 1200px;
    height: 900px;
    display: flex;
    align-items: center;
    justify-content: center;
  }
  .business-card {
    position: relative;
    width: 1050px;
    height: 600px;
    background: var(--card);
    box-shadow: 0 6px 24px rgba(0, 0, 0, 0.12);
    padding: 60px 70px;
  }
  .brand {
    display: flex;
    align-items: center;
    gap: 18px;
  }
  .brand-dot {
    width: 54px;
    height: 54px;
    border-radius: 50%;
    background: var(--brand-blue);
  }
  .brand-name {
    font-weight: 400;
    font-size: 34px;
    letter-spacing: 3px;
    color: var(--ink);
    text-transform: uppercase;
  }
  .person {
    margin-top: 62px;
  }
  .person-name {
    font-weight: 900;
    font-size: 62px;
    line-height: 1;
    color: var(--brand-blue);
  }
  .person-title {
    margin-top: 12px;
    font-size: 28px;
    font-weight: 400;
  }
  .address {
    margin-top: 34px;
    font-size: 27px;
    line-height: 1.25;
  }
  .contact-list {
    list-style: none;
    margin-top: 22px;
  }
  .contact-item {
    display: flex;
    align-items: center;
    gap: 18px;
    font-size: 26px;
    line-height: 1.3;
  }
  .contact-icon {
    width: 24px;
    height: 24px;
    flex: none;
    fill: var(--brand-blue);
  }
  .accent { color: var(--brand-blue); }
</style>
</head>
<body>
<main class="stage">
  <article class="business-card">
    <header class="brand">
      <span class="brand-dot"></span>
      <span class="brand-name">Delmar Hollis + Partners</span>
    </header>

    <section class="person">
      <h1 class="person-name">Grant Ellison</h1>
      <p class="person-title">Partner / Director of Design</p>
    </section>

    <address class="address" style="font-style: normal;">
      412 Corvell<br>
      West Palm Beach 33401
    </address>

    <ul class="contact-list">
      <li class="contact-item">
        <svg class="contact-icon" viewBox="0 0 24 24" aria-hidden="true">
          <path d="M3 6c0-1.5 2-3 9-3s9 1.5 9 3v2h-5V6.5c-1-.4-2.5-.5-4-.5s-3 .1-4 .5V8H3z"/>
          <path d="M6 10h12l2 10H4z"/>
          <circle cx="12" cy="15" r="2.6" fill="#fff"/>
        </svg>
        <span>561.555.0142</span>
      </li>
      <li class="contact-item">
        <svg class="contact-icon" viewBox="0 0 24 24" aria-hidden="true">
          <path d="M7 1h10a2 2 0 0 1 2 2v18a2 2 0 0 1-2 2H7a2 2 0 0 1-2-2V3a2 2 0 0 1 2-2zm0 3v15h10V4z"/>
        </svg>
        <span>561.555.0178</span>
      </li>
      <li class="contact-item">
        <svg class="contact-icon" viewBox="0 0 24 24" aria-hidden="true">
          <path d="M1 5h22v14H1z"/>
          <path d="M2 6l10 7 10-7" fill="none" stroke="#fff" stroke-width="1.6"/>
        </svg>
        <span>grant@delmarhollis.example</span>
      </li>
      <li class="contact-item">
        <svg class="contact-icon" viewBox="0 0 24 24" aria-hidden="true">
          <circle cx="12" cy="12" r="10.5"/>
          <g fill="none" stroke="#fff" stroke-width="1.2">
            <ellipse cx="12" cy="12" rx="4.5" ry="10"/>
            <path d="M2 12h20M3.5 7h17M3.5 17h17M12 2v20"/>
          </g>
        </svg>
        <span>www.<span class="accent">delmarhollis</span>.example</span>
      </li>
    </ul>
  </article>
</main>
</body>
</html>
```